Business Card - connecting 2 souls and beggining the journey of self discovery

Logo on the front
with tag line

On the back list of services and contact details

Seminars
workshops
Coaching
podcasts

Darren Whitlow
Health & Wellbeing Life Coach
0491 372 615
darren@brightcoreliving.example
brightcoreliving.example

Industry/Entity Type

Life Coaching

Contact Information for Business Card

I like the use of colour from the logo to be used. I'm not a fan of white.

Requirements
Must have
• My tagline: The journey home starts with you
Nice to have
• Use of colour that is in the mind body soul logo

```html
<!DOCTYPE html>
<html lang="en">
<head>
<meta charset="utf-8">
<title>Brightcore Living – Business Card</title>
<link rel="stylesheet" href="https://fonts.googleapis.com/css2?family=Open+Sans:wght@400;600;700&display=swap">
<style>
  :root {
    --backdrop: #2e2a28;
    --card: #151515;
    --card-edge: #222222;
    --ink-white: #f2f2f2;
    --ink-grey: #8d8d8d;
    --teal: #3fbf92;
    --coral: #ef5a5f;
    --mark: #9a5fc4;
    --divider: #9a9a9a;
  }
  * { box-sizing: border-box; margin: 0; padding: 0; }
  html, body { width: 1200px; height: 864px; overflow: hidden; }
  body {
    background: var(--backdrop);
    font-family: "Open Sans", Arial, sans-serif;
    display: flex;
    flex-direction: column;
    align-items: center;
    justify-content: center;
    gap: 30px;
  }
  .card {
    width: 680px;
    height: 389px;
    background: var(--card);
    border: 1px solid var(--card-edge);
    border-radius: 4px;
    position: relative;
    overflow: hidden;
  }

  /* Front */
  .card--front {
    display: flex;
    flex-direction: column;
    align-items: center;
    justify-content: center;
  }
  .brand-dot {
    width: 84px; height: 84px;
    border-radius: 50%;
    background: var(--mark);
  }
  .card--front .brand-name {
    margin-top: 22px;
    font-size: 40px;
    font-weight: 600;
    letter-spacing: -1.5px;
    color: var(--ink-grey);
  }
  .services {
    margin-top: 12px;
    list-style: none;
    display: flex;
    gap: 10px;
    font-size: 17px;
    color: var(--ink-white);
  }
  .services li + li::before {
    content: "";
    display: inline-block;
    width: 6px; height: 6px;
    border-radius: 50%;
    background: var(--teal);
    margin-right: 10px;
    vertical-align: middle;
  }

  /* Back */
  .card--back { display: flex; align-items: center; }
  .identity {
    width: 50%;
    padding-left: 50px;
    display: flex;
    flex-direction: column;
    align-items: flex-start;
  }
  .identity .brand-dot { width: 74px; height: 74px; margin-left: 130px; }
  .identity .brand-name {
    margin-top: 16px;
    font-size: 33px;
    font-weight: 600;
    letter-spacing: -1.2px;
    color: var(--ink-white);
  }
  .tagline {
    font-size: 17px;
    font-weight: 600;
    color: var(--ink-white);
    margin-top: 2px;
  }
  .divider {
    width: 2px;
    height: 220px;
    background: linear-gradient(to bottom, transparent, var(--divider), transparent);
  }
  .contact {
    padding-left: 36px;
    display: flex;
    flex-direction: column;
  }
  .contact-name {
    font-size: 26px;
    font-weight: 700;
    text-transform: uppercase;
    color: var(--teal);
    letter-spacing: 0.5px;
  }
  .contact-role {
    font-size: 14.5px;
    font-weight: 700;
    text-transform: uppercase;
    color: var(--coral);
    margin-bottom: 26px;
  }
  .contact-list { list-style: none; }
  .contact-list li {
    display: flex;
    align-items: center;
    gap: 10px;
    font-size: 17px;
    color: var(--ink-white);
    line-height: 1.5;
  }
  .contact-list svg { width: 15px; height: 15px; flex: none; }
</style>
</head>
<body>

  <section class="card card--front" aria-label="Card front">
    <span class="brand-dot" aria-hidden="true"></span>
    <h1 class="brand-name">Brightcore Living</h1>
    <ul class="services">
      <li>Seminars</li>
      <li>Workshops</li>
      <li>Coaching</li>
      <li>Podcasts</li>
    </ul>
  </section>

  <section class="card card--back" aria-label="Card back">
    <div class="identity">
      <span class="brand-dot" aria-hidden="true"></span>
      <h2 class="brand-name">Brightcore Living</h2>
      <p class="tagline">The journey home starts with you</p>
    </div>
    <div class="divider" aria-hidden="true"></div>
    <div class="contact">
      <p class="contact-name">Darren Whitlow</p>
      <p class="contact-role">Health &amp; Wellbeing Life Coach</p>
      <ul class="contact-list">
        <li>
          <svg viewBox="0 0 16 16" aria-hidden="true"><path fill="var(--teal)" d="M3.5 1.5l2.6 2.8-1.4 1.9c.9 2 2.4 3.6 4.5 4.6l1.9-1.4 2.8 2.6-1.6 2.1C6.8 13.5 2.3 9 1.4 3.1z"/></svg>
          0491 372 615
        </li>
        <li>
          <svg viewBox="0 0 16 16" aria-hidden="true"><rect x="1" y="3" width="14" height="10" rx="1.5" fill="var(--teal)"/><path d="M1.5 4l6.5 5 6.5-5" stroke="var(--card)" stroke-width="1.3" fill="none"/></svg>
          darren@brightcoreliving.example
        </li>
        <li>
          <svg viewBox="0 0 16 16" aria-hidden="true"><circle cx="8" cy="8" r="7" fill="var(--teal)"/><path d="M1 8h14M8 1c-3 3.5-3 10.5 0 14M8 1c3 3.5 3 10.5 0 14" stroke="var(--card)" stroke-width="1.1" fill="none"/></svg>
          brightcoreliving.example
        </li>
      </ul>
    </div>
  </section>

</body>
</html>
```